Vantor Ridge needs a Business Card Design

We need a business card design for an Information Technology company based in Fairfax Virginia called Vantor Ridge. We want the business card to use our logo colors. We need it to be double-sided. The business card needs to look professional but we would like it to be unique. You can get company information from our web site (http://www.vantorridgellc.example).

Target Market(s)

Target market is Government Agencies and Business Professionals.

Industry/Entity Type

Business

Requirements
Must have
• Must have section for company name, company address, company URL, employee name, title, phone and email. Also must have company logo and space for entering logos.

```html
<!DOCTYPE html>
<html lang="en">
<head>
<meta charset="utf-8">
<title>Vantor Ridge – Business Card</title>
<link rel="stylesheet" href="https://fonts.googleapis.com/css2?family=Open+Sans:wght@400;600;700&display=swap">
<style>
:root{
  --stage:#e9e6e1;
  --navy:#1b2a8a;
  --royal:#2336a8;
  --blue-light:#2c49b8;
  --accent:#1e7fd0;
  --white:#ffffff;
  --ink-soft:#dfe6ff;
  --rule:#7f96e6;
}
*{box-sizing:border-box;margin:0;padding:0}
html,body{width:1200px;height:1024px;overflow:hidden}
body{background:var(--stage);font-family:"Open Sans",sans-serif;position:relative}
.card{position:absolute;left:250px;width:700px;height:400px;overflow:hidden;box-shadow:0 10px 28px rgba(0,0,0,.22)}
.card-front{top:60px;background:var(--white)}
.card-back{top:552px;background:linear-gradient(160deg,var(--blue-light) 0%,var(--royal) 45%,var(--navy) 100%)}

.brand{display:flex;align-items:center;gap:16px}
.brand-mark{width:34px;height:34px;flex:none;background:var(--royal)}
.brand-name{font-weight:700;font-size:40px;letter-spacing:1px;text-transform:uppercase;color:var(--royal);line-height:1;white-space:nowrap}
.brand-tagline{font-size:11px;letter-spacing:.6px;text-transform:uppercase;color:var(--navy);margin-top:6px;white-space:nowrap}

/* front */
.front-brand{position:absolute;left:70px;top:0;height:196px}
.front-rule{position:absolute;left:0;top:196px;width:100%;height:6px;background:var(--accent);border-top:2px solid var(--white)}
.front-panel{position:absolute;left:0;top:202px;width:100%;height:198px;background:linear-gradient(170deg,var(--blue-light),var(--navy))}
.person{position:absolute;left:40px;bottom:30px;color:var(--white)}
.person-name{font-weight:700;font-size:20px}
.person-title{font-size:13px;color:var(--ink-soft);margin-top:2px}
.contact-divider{position:absolute;left:380px;top:30px;width:1px;height:140px;background:linear-gradient(var(--rule),transparent)}
.contact-list{position:absolute;left:405px;top:28px;list-style:none;color:var(--white);font-size:13px;line-height:1.5}
.contact-list li{display:flex;align-items:flex-start;gap:8px;white-space:nowrap}
.contact-list li.gap{margin-top:10px}
.contact-list svg{width:12px;height:12px;margin-top:4px;flex:none;fill:var(--white)}

/* back */
.back-brand{position:absolute;left:0;top:0;width:100%;height:100%;justify-content:center}
.back-brand .brand-mark{background:var(--white)}
.back-brand .brand-name{color:var(--white)}
.back-brand .brand-tagline{color:var(--ink-soft)}
.back-url{position:absolute;left:40px;bottom:34px;color:var(--white);font-size:13px}
</style>
</head>
<body>

<section class="card card-front" aria-label="Business card front">
  <div class="brand front-brand">
    <span class="brand-mark"></span>
    <div>
      <div class="brand-name">Vantor Ridge</div>
      <div class="brand-tagline">Delivering clarity through technology</div>
    </div>
  </div>
  <div class="front-rule"></div>
  <div class="front-panel">
    <div class="person">
      <div class="person-name">Daniel Morwen</div>
      <div class="person-title">Job Title</div>
    </div>
    <div class="contact-divider"></div>
    <ul class="contact-list">
      <li><svg viewBox="0 0 12 12"><path d="M6 1L1 6h2v5h6V6h2z"/></svg><span>4180 Larkspur Ave, Suite 310<br>Fairfax, VA 22030</span></li>
      <li class="gap"><svg viewBox="0 0 12 12"><path d="M2 1h3l1 3-2 1a7 7 0 0 0 3 3l1-2 3 1v3c-6 0-9-3-9-9z"/></svg><span>877.555.0142</span></li>
      <li><svg viewBox="0 0 12 12"><rect x="2" y="1" width="8" height="10" rx="1"/></svg><span>888.555.0187</span></li>
      <li><svg viewBox="0 0 12 12"><path d="M1 3h10v7H1z M1 3l5 4 5-4" stroke="#1b2a8a" stroke-width=".8"/></svg><span>name@vantorridge.example</span></li>
      <li><svg viewBox="0 0 12 12"><circle cx="6" cy="6" r="5"/></svg><span>www.vantorridgellc.example</span></li>
    </ul>
  </div>
</section>

<section class="card card-back" aria-label="Business card back">
  <div class="brand back-brand">
    <span class="brand-mark"></span>
    <div>
      <div class="brand-name">Vantor Ridge</div>
      <div class="brand-tagline">Delivering clarity through technology</div>
    </div>
  </div>
  <div class="back-url">www.vantorridgellc.example</div>
</section>

</body>
</html>
```